Carpet cleaning company focused on high quality needs business cards

We are a growing company that just merged with another company and need to design a new business card. We do both residential as well as commercial cleaning. We do carpet, tile & grout, upholstery, hard floors, and stain & pet odor removal. We treat our customers like family and strive to achieve outstanding results with every job.

```html
<!DOCTYPE html>
<html lang="en">
<head>
<meta charset="utf-8">
<title>Brightway Steam Cleaning – Business Cards</title>
<link href="https://fonts.googleapis.com/css2?family=Montserrat:wght@400;500;700;900&display=swap" rel="stylesheet">
<style>
  :root {
    --stage: #1c1d20;
    --card-dark: #2f3034;
    --card-light: #ffffff;
    --ink: #161616;
    --ink-soft: #2a2a2a;
    --accent-red: #e8403a;
    --on-dark: #ffffff;
  }
  * { box-sizing: border-box; margin: 0; padding: 0; }
  html, body {
    width: 1200px; height: 900px; overflow: hidden;
    background: var(--stage);
    font-family: "Montserrat", sans-serif;
  }
  .canvas {
    position: relative; width: 1200px; height: 900px;
    display: flex; align-items: center; justify-content: center; gap: 60px;
  }
  .card {
    position: relative; width: 525px; height: 300px;
    border-radius: 22px; overflow: hidden;
    box-shadow: 0 18px 40px rgba(0,0,0,.45);
  }

  /* back */
  .card--back {
    background: var(--card-dark);
    display: flex; align-items: center; justify-content: center; gap: 18px;
  }
  .brand-mark { width: 46px; height: 46px; background: var(--accent-red); flex: none; }
  .brand-name {
    color: var(--on-dark); font-weight: 900; text-transform: uppercase;
    font-size: 30px; line-height: 1.02; letter-spacing: .5px;
  }

  /* front */
  .card--front { background: var(--card-light); }
  .hero-art {
    position: absolute; left: 0; bottom: 0; width: 270px; height: 200px; display: block;
  }
  .details {
    position: absolute; left: 285px; top: 34px; right: 20px;
    color: var(--ink);
  }
  .details .brand-name { color: var(--ink); font-size: 21px; line-height: 1.05; margin-bottom: 14px; }
  .person-name {
    color: var(--accent-red); font-weight: 700; font-size: 22px; line-height: 1.1;
  }
  .person-role { font-size: 12px; font-weight: 500; margin: 4px 0 10px; color: var(--ink-soft); }
  .address { font-size: 11.5px; line-height: 1.4; color: var(--ink-soft); margin-bottom: 10px; }
  .contact-list { list-style: none; }
  .contact-list li {
    display: flex; align-items: center; gap: 8px;
    font-size: 11.5px; line-height: 1.6; color: var(--ink-soft);
  }
  .contact-icon { width: 11px; height: 11px; flex: none; display: block; }
</style>
</head>
<body>
<main class="canvas">

  <section class="card card--back" aria-label="Business card back">
    <span class="brand-mark"></span>
    <p class="brand-name">Brightway<br>Steam<br>Cleaning</p>
  </section>

  <section class="card card--front" aria-label="Business card front">
    <svg class="hero-art" viewBox="0 0 270 200" role="img"
         aria-label="Illustration of a cheerful cleaning technician with a steam wand against a red burst panel">
      <defs>
        <linearGradient id="heroFill" x1="0" y1="0" x2="1" y2="1">
          <stop offset="0" stop-color="#4e9bd2"/>
          <stop offset="1" stop-color="#c9a46a"/>
        </linearGradient>
      </defs>
      <polygon points="200,20 265,200 110,200" fill="#e8403a"/>
      <rect x="0" y="40" width="190" height="160" fill="url(#heroFill)" opacity=".85"/>
    </svg>

    <div class="details">
      <p class="brand-name">Brightway<br>Steam Cleaning</p>
      <p class="person-name">Daniel Harper</p>
      <p class="person-role">CEO</p>
      <p class="address">418 Maple Grove Ave, #112<br>Fairview, OH 43199</p>
      <ul class="contact-list">
        <li><svg class="contact-icon" viewBox="0 0 12 12" aria-hidden="true"><path fill="#e8403a" d="M2 1h3l1 3-2 1a7 7 0 0 0 3 3l1-2 3 1v3c-6 0-9-3-9-9z"/></svg>555 017-2840</li>
        <li><svg class="contact-icon" viewBox="0 0 12 12" aria-hidden="true"><path fill="#e8403a" fill-rule="evenodd" d="M3 0h6v12H3z M4 1.5v8h4v-8z"/></svg>555 017-2840</li>
        <li><svg class="contact-icon" viewBox="0 0 12 12" aria-hidden="true"><path fill="#e8403a" fill-rule="evenodd" d="M0 2h12v8H0z M1.5 3.2l4.5 3.4 4.5-3.4z"/></svg>info@brightwaysteam.com</li>
        <li><svg class="contact-icon" viewBox="0 0 12 12" aria-hidden="true"><circle fill="#e8403a" cx="6" cy="6" r="5.5"/></svg>www.brightwaysteam.com</li>
      </ul>
    </div>
  </section>

</main>
</body>
</html>
```